Copper Ridge Inquiries Letterhead

I would like to design a letterhead for a private investigation company. Our primary clients will be law firms. The business card is included below

```html
<!DOCTYPE html>
<html lang="en">
<head>
<meta charset="utf-8">
<title>Copper Ridge Inquiries Letterhead</title>
<link href="https://fonts.googleapis.com/css2?family=Montserrat:wght@400;500;700;800&family=Lato:wght@400;700&family=Dancing+Script:wght@600&display=swap" rel="stylesheet">
<style>
  :root {
    --navy: #1d3566;
    --orange: #f0612d;
    --ink: #1e1e1e;
    --muted: #3a3a3a;
    --paper: #ffffff;
    --backdrop: #e4e4e4;
  }
  * { box-sizing: border-box; margin: 0; padding: 0; }
  html, body {
    width: 1200px; height: 960px; overflow: hidden;
    background: var(--backdrop);
  }
  .letterhead {
    position: absolute; left: 275px; top: 20px;
    width: 650px; height: 920px;
    background: var(--paper);
    box-shadow: 0 6px 24px rgba(0,0,0,.12);
    font-family: "Lato", sans-serif;
    color: var(--ink);
    overflow: hidden;
  }
  .brand {
    position: absolute; left: 48px; top: 52px;
    display: flex; align-items: center; gap: 10px;
  }
  .brand-dot {
    width: 28px; height: 28px; border-radius: 50%;
    background: var(--orange); flex: none;
  }
  .brand-name {
    font-family: "Montserrat", sans-serif; font-weight: 800;
    font-size: 18px; letter-spacing: .4px; color: var(--navy);
    text-transform: uppercase; line-height: 1.1; white-space: nowrap;
  }
  .contact {
    position: absolute; left: 392px; top: 48px;
    padding-left: 22px;
    font-family: "Montserrat", sans-serif; font-size: 9.5px;
    letter-spacing: .3px; color: var(--navy); text-transform: uppercase;
    white-space: nowrap;
  }
  .contact::before {
    content: ""; position: absolute; left: 0; top: 8px;
    width: 1.5px; height: 44px; background: var(--orange);
  }
  .contact-row { display: flex; align-items: center; gap: 7px; line-height: 19px; }
  .contact-row svg { width: 10px; height: 10px; fill: var(--orange); flex: none; }
  .letter {
    position: absolute; left: 56px; top: 200px; width: 540px;
    font-size: 13.5px; line-height: 1.45; color: var(--muted);
  }
  .date, .recipient { font-family: "Montserrat", sans-serif; font-size: 14px; color: var(--ink); }
  .date { margin-bottom: 22px; }
  .recipient { margin-bottom: 18px; line-height: 1.35; }
  .recipient + .recipient { margin-bottom: 20px; }
  .salutation {
    font-family: "Montserrat", sans-serif; font-weight: 700;
    font-size: 18px; color: var(--ink); margin-bottom: 14px;
  }
  .letter p.body { margin-bottom: 20px; }
  .closing { font-family: "Montserrat", sans-serif; font-size: 14px; margin-top: 14px; color: var(--ink); }
  .signature {
    font-family: "Dancing Script", cursive; font-weight: 600;
    font-size: 40px; color: #111; margin-top: 40px; margin-left: 10px;
  }
  .footer {
    position: absolute; left: 0; bottom: 0; width: 650px; height: 38px;
    font-family: "Montserrat", sans-serif; font-size: 10.5px; letter-spacing: .3px;
    color: #fff; text-transform: uppercase;
  }
  .footer svg { position: absolute; inset: 0; }
  .footer-text {
    position: absolute; top: 0; bottom: 0; margin: auto;
    height: 24px; line-height: 24px; white-space: nowrap;
  }
  .license { left: 60px; }
  .experience { left: 296px; width: 300px; text-align: center; }
</style>
</head>
<body>
  <article class="letterhead">
    <header>
      <div class="brand">
        <span class="brand-dot"></span>
        <span class="brand-name">Copper Ridge Inquiries</span>
      </div>
      <div class="contact">
        <div class="contact-row">
          <svg viewBox="0 0 10 10"><path d="M5 0a3.6 3.6 0 0 0-3.6 3.6C1.4 6.2 5 10 5 10s3.6-3.8 3.6-6.4A3.6 3.6 0 0 0 5 0zm0 5a1.4 1.4 0 1 1 0-2.8A1.4 1.4 0 0 1 5 5z"/></svg>
          Fort Alder, TX
        </div>
        <div class="contact-row">
          <svg viewBox="0 0 10 10"><path d="M2 .5l2 2-1 1.3c.6 1.3 1.6 2.3 2.9 2.9L7.2 5.7l2 2-1.4 1.8C4 9 1 6 .4 2z"/></svg>
          210.555.0147
        </div>
        <div class="contact-row">
          <svg viewBox="0 0 10 10"><path d="M0 2h10v6H0zM.8 2.6 5 5.6l4.2-3V3.5L5 6.5.8 3.5z"/></svg>
          dana@copperridgeinquiries.com
        </div>
      </div>
    </header>

    <main class="letter">
      <p class="date">January-03-2020</p>
      <p class="recipient">Mr. John Doe<br>President</p>
      <p class="recipient">Halden Corporation<br>123 Street Name, Suite# 10<br>City, State, 120023</p>
      <p class="salutation">Dear Mr. John</p>
      <p class="body">Lorem ipsum dolor sit amet, consectetur adipiscing elit, sed do eiusmod tempor incididunt ut labore et dolore magna aliqua. Ut enim ad minim veniam, quis nostrud exercitation ullamco laboris nisi ut aliquip ex ea commodo consequat. Duis aute irure dolor in reprehenderit in voluptate velit esse cillum dolore eu fugiat nulla pariatur.</p>
      <p class="body">Lorem ipsum dolor sit amet, consectetur adipiscing elit, sed do eiusmod tempor incididunt ut labore et dolore magna aliqua. Ut enim ad minim veniam, quis nostrud exercitation ullamco laboris nisi ut aliquip ex ea commodo consequat. Duis aute irure dolor in reprehenderit in voluptate velit esse cillum dolore eu fugiat nulla pariatur.</p>
      <p class="body">Lorem ipsum dolor sit amet, consectetur adipiscing elit, sed do eiusmod tempor incididunt ut labore et dolore magna aliqua. Ut enim ad minim veniam, quis nostrud exercitation ullamco laboris nisi ut aliquip ex ea commodo consequat.</p>
      <p class="body">Excepteur sint occaecat cupidatat non proident, sunt in culpa qui officia deserunt mollit anim id est laborum. re et dolore magnam aliquam quaerat voluptatem.</p>
      <p class="closing">Regards</p>
      <p class="signature">Dana Whitlow</p>
    </main>

    <footer class="footer">
      <svg viewBox="0 0 650 38" width="650" height="38" aria-hidden="true">
        <polygon points="0,0 292,0 280,38 0,38" fill="var(--navy)"/>
        <polygon points="300,0 604,0 592,38 288,38" fill="var(--orange)"/>
        <polygon points="612,0 650,0 650,38 600,38" fill="var(--navy)"/>
      </svg>
      <span class="footer-text license">License No. 04720316</span>
      <span class="footer-text experience">Over 20 years of investigative experince</span>
    </footer>
  </article>
</body>
</html>
```